80s style fun billboard for auto repair shop

A new design for our automotive shops’s advertisement billboard with an 80s-90s theme! Neon colors like photo example. Something eye catching but easy to read. Logos attached should be altered to match theme of advertisement. 1980s or 90s colors and theme. Details need to include an arrow and “1.2 miles ahead”, phone number “817-390-7148”, address “2085 W Malbury St”, and “best auto repair shop in town!” . Dimensions are 12'3"x 24'6"

Target Market(s)

Drive by attention

Industry/Entity Type

Automotive

Colors

Designer to choose colors to be used in the design.

Requirements
Must have
• My logo, address, phone number, tag line and badass 90s theme look!
Nice to have
• 80s color scheme, neon colors, use example photo for color ideas

```html
<!DOCTYPE html>
<html lang="en">
<head>
<meta charset="utf-8">
<title>Ashford's Premier Auto &amp; Diesel Billboard</title>
<link rel="stylesheet" href="https://fonts.googleapis.com/css2?family=Krona+One&family=Poppins:wght@800&family=Barlow+Condensed:ital,wght@1,600&family=Montserrat:wght@700&display=swap">
<style>
  :root {
    --page: #16161c;
    --navy: #0c1238;
    --navy-deep: #070b26;
    --purple: #3a1a6e;
    --cyan: #35f0e6;
    --cyan-glow: #19d9ff;
    --magenta: #ff4fe6;
    --yellow: #ffee2a;
    --neon-red: #ff2a3a;
    --white: #ffffff;
    --band-a: #3a86d6;
    --band-b: #5aa7ea;
    --photo-a: #cfc8bc;
    --photo-b: #e8862a;
    --badge: #2f7fd0;
  }
  html, body { margin: 0; height: 100%; overflow: hidden; }
  body {
    width: 1040px; height: 1200px;
    background: var(--page);
    display: flex; align-items: center; justify-content: center;
  }
  .billboard { width: 1040px; height: 522px; display: block; }
  .headline { font-family: "Krona One", sans-serif; fill: none; stroke: var(--cyan); stroke-width: 2.2; filter: drop-shadow(0 0 4px var(--cyan-glow)); }
  .service { font-family: "Krona One", sans-serif; fill: none; stroke: var(--magenta); stroke-width: 1.8; filter: drop-shadow(0 0 4px var(--magenta)); }
  .phone { font-family: "Poppins", sans-serif; font-weight: 800; fill: var(--cyan); }
  .distance { font-family: "Barlow Condensed", sans-serif; font-style: italic; font-weight: 600; fill: var(--white); }
  .address { font-family: "Montserrat", sans-serif; font-weight: 700; fill: var(--white); letter-spacing: 6px; }
  .brand-name { font-family: "Poppins", sans-serif; font-weight: 800; fill: var(--navy); }
  .neon-line { fill: none; stroke: var(--cyan); stroke-width: 2.5; filter: drop-shadow(0 0 3px var(--cyan-glow)); }
  .bolt { fill: none; stroke: var(--yellow); stroke-width: 2.5; stroke-linejoin: miter; filter: drop-shadow(0 0 3px var(--yellow)); }
  .arrow-outer { fill: none; stroke: var(--neon-red); stroke-width: 3; filter: drop-shadow(0 0 4px var(--neon-red)); }
  .arrow-inner { fill: none; stroke: var(--yellow); stroke-width: 2; }
</style>
</head>
<body>
<svg class="billboard" viewBox="0 0 1040 522" xmlns="http://www.w3.org/2000/svg">
  <defs>
    <linearGradient id="bgGrad" x1="0" y1="0" x2="1" y2="0">
      <stop offset="0" stop-color="var(--navy)"/>
      <stop offset="0.55" stop-color="var(--purple)"/>
      <stop offset="1" stop-color="var(--navy-deep)"/>
    </linearGradient>
    <pattern id="stripes" width="10" height="12" patternUnits="userSpaceOnUse">
      <rect y="5" width="10" height="1.5" fill="#8a4fe0" opacity="0.35"/>
    </pattern>
    <linearGradient id="bandGrad" x1="0" y1="0" x2="1" y2="0">
      <stop offset="0" stop-color="var(--band-a)"/>
      <stop offset="1" stop-color="var(--band-b)"/>
    </linearGradient>
    <linearGradient id="photoGrad" x1="0" y1="0" x2="0.6" y2="1">
      <stop offset="0" stop-color="var(--photo-a)"/>
      <stop offset="0.55" stop-color="var(--photo-b)"/>
      <stop offset="1" stop-color="#b9b6b2"/>
    </linearGradient>
    <radialGradient id="mascotGrad">
      <stop offset="0" stop-color="#f3eeee"/>
      <stop offset="1" stop-color="#ffffff"/>
    </radialGradient>
    <clipPath id="canvasClip"><rect width="1040" height="522"/></clipPath>
  </defs>

  <g clip-path="url(#canvasClip)">
    <!-- Background -->
    <rect class="backdrop" width="1040" height="522" fill="url(#bgGrad)"/>
    <rect class="backdrop-stripes" x="300" y="140" width="320" height="330" fill="url(#stripes)"/>

    <!-- Neon frame lines -->
    <path class="neon-line" d="M45 56 H543 L513 167"/>
    <path class="neon-line" d="M482 137 H566 M461 159 H545"/>

    <!-- Lightning bolt -->
    <path class="bolt" d="M107 134 L75 192 L99 192 L29 258 M99 192 L75 221"/>

    <!-- Headline -->
    <text class="headline" x="57" y="128" font-size="66" textLength="434" lengthAdjust="spacingAndGlyphs">Ashford's</text>
    <text class="headline" x="112" y="200" font-size="66" textLength="330" lengthAdjust="spacingAndGlyphs">Premier</text>

    <!-- Service line -->
    <text class="service" x="116" y="253" font-size="40" textLength="305" lengthAdjust="spacingAndGlyphs">auto &amp; diesel</text>
    <text class="service" x="134" y="297" font-size="40" textLength="270" lengthAdjust="spacingAndGlyphs">repair shop</text>

    <!-- Phone -->
    <text class="phone" x="87" y="360" font-size="54" textLength="362" lengthAdjust="spacingAndGlyphs">817-390-7148</text>

    <!-- Arrow + distance -->
    <path class="arrow-outer" d="M42 399 H103 L98 384 L141 416 L104 446 L106 430 L62 430 Z"/>
    <path class="arrow-inner" d="M52 405 H110 L107 396 L130 416 L110 434 L111 424 L66 424 Z"/>
    <text class="distance" x="165" y="428" font-size="44" textLength="226" lengthAdjust="spacingAndGlyphs">1.2 Miles Ahead</text>

    <!-- Photo circle with rings -->
    <circle class="outer-ring" cx="1030" cy="500" r="500" fill="var(--white)"/>
    <circle class="inner-ring" cx="1030" cy="500" r="486" fill="var(--navy)"/>
    <circle class="ring-gap" cx="1030" cy="500" r="476" fill="var(--white)"/>
    <circle class="service-photo" cx="1030" cy="500" r="466" fill="url(#photoGrad)" role="img" aria-label="Photo of an orange pickup truck with its hood open in a repair garage"/>

    <!-- Address band -->
    <path class="address-band" d="M0 465 H570 Q590 493 600 522 H0 Z" fill="url(#bandGrad)"/>
    <path class="pin-icon" d="M121 483 a8 8 0 0 1 16 0 c0 7 -8 16 -8 16 s-8 -9 -8 -16 z" fill="var(--white)"/>
    <circle cx="129" cy="483" r="3" fill="var(--band-a)"/>
    <text class="address" x="147" y="502" font-size="22" textLength="290" lengthAdjust="spacingAndGlyphs">2085 W Malbury St</text>

    <!-- Brand name plate -->
    <path class="brand-plate" d="M735 40 Q870 -10 1040 40 V150 Q880 200 735 150 Z" fill="var(--white)" opacity="0.95"/>
    <text class="brand-name" x="790" y="108" font-size="30" textLength="170" lengthAdjust="spacingAndGlyphs">JT's Auto Lube</text>

    <!-- Mascot circle -->
    <circle class="mascot" cx="572" cy="405" r="99" fill="url(#mascotGrad)" role="img" aria-label="Cartoon mechanic mascot holding a wrench and an oil can"/>

    <!-- Certification badge -->
    <circle class="cert-badge" cx="969" cy="456" r="41" fill="var(--badge)"/>
  </g>
</svg>
</body>
</html>
```